Bry7Legal Letterhead

Need a new letterhead for my law firm.
IDENTIFYING INFORMATION BELOW:
Anselmo R Quintara III
Attorney at Law
Address: 2847 Larkspur Blvd, Ste 300, Dallas, TX 75204
Phone: 877-482-6017
Fax: 469-738-1452
Email: bry@bry7legal.example
Website: www.bry7legal.example

Colors
0054AA
0677BA
7BADD7
CADEEF
E8F1F8

Requirements
Must have
• Logo needs to be on the letterhead, along with identifying information which is included in the project description.

```html
<!DOCTYPE html>
<html lang="en">
<head>
<meta charset="utf-8">
<title>Bry7Legal Letterhead</title>
<link rel="stylesheet" href="https://fonts.googleapis.com/css2?family=Arimo:wght@400;700&display=swap">
<style>
  :root {
    --blue-deep: #0054AA;
    --blue-mid: #0677BA;
    --blue-soft: #7BADD7;
    --blue-pale: #CADEEF;
    --ink: #2a2a2a;
    --ink-soft: #555;
    --rule: #9a9a9a;
    --black: #111;
    --paper: #fbfbfb;
    --backdrop: #e9e9ea;
  }
  * { box-sizing: border-box; margin: 0; padding: 0; }
  html, body { width: 1200px; height: 795px; overflow: hidden; }
  body {
    background: var(--backdrop);
    font-family: "Arimo", Arial, sans-serif;
    color: var(--ink);
    position: relative;
  }
  .letterhead {
    position: absolute;
    left: 333px; top: 20px;
    width: 534px; height: 755px;
    background: var(--paper);
    box-shadow: 0 2px 10px rgba(0,0,0,.12);
    overflow: hidden;
  }
  .brand {
    position: absolute; left: 62px; top: 72px;
    display: flex; align-items: center; gap: 6px;
  }
  .brand-mark { width: 12px; height: 12px; background: var(--blue-mid); }
  .brand-name { font-weight: 700; font-size: 21px; color: var(--black); letter-spacing: .5px; }

  .letter {
    position: absolute; left: 62px; top: 190px; width: 410px;
    font-size: 8px; line-height: 1.45; color: var(--ink);
  }
  .letter-date { margin-bottom: 12px; }
  .recipient { font-style: normal; margin-bottom: 14px; }
  .salutation { margin-bottom: 12px; }
  .letter-body p { margin-bottom: 12px; }
  .closing { margin-top: 16px; color: var(--ink-soft); }
  .signature {
    display: block; margin-top: 6px;
    width: 150px; height: 24px;
    background: linear-gradient(90deg, #d6d6d6, #eeeeee);
  }

  .contact-row {
    position: absolute; left: 62px; bottom: 36px;
    display: flex; align-items: center; gap: 14px;
    font-size: 8px; line-height: 1.6; white-space: nowrap;
  }
  .attorney-name { color: var(--blue-deep); font-weight: 700; }
  .divider { width: 1px; height: 18px; background: var(--rule); }
  .contact-list { list-style: none; }
  .contact-list li { display: flex; align-items: center; gap: 4px; }
  .contact-list svg { width: 7px; height: 7px; fill: var(--blue-deep); flex: none; }

  .footer-band {
    position: absolute; left: 0; right: 0; bottom: 0; height: 22px;
    background: var(--blue-deep);
    color: #fff; font-size: 8px; white-space: nowrap;
    display: flex; align-items: center; padding-left: 92px;
  }
  .footer-mark {
    position: absolute; right: 66px; bottom: 22px;
    width: 20px; height: 20px; background: var(--blue-mid);
  }
  .footer-block {
    position: absolute; right: 0; bottom: 22px;
    width: 64px; height: 32px; background: var(--black);
  }
</style>
</head>
<body>
  <main class="letterhead">
    <header class="brand">
      <span class="brand-mark"></span>
      <span class="brand-name">Bry7Legal</span>
    </header>

    <section class="letter">
      <p class="letter-date">01 January 2050</p>
      <address class="recipient">
        Company (Pvt) Ltd.<br>PO Box 3355 Mainville St<br>Sample City Country 3355
      </address>
      <p class="salutation">Dear Harold Brixton,</p>
      <div class="letter-body">
        <p>Lorem ipsum dolor sit amet, consectetuer adipiscing elit, sed diam nonummy nibh euismod tincidunt ut laoreet dolore magna aliquam erat volutpat. Ut wisi enim ad minim veniam, quis nostrud exerci tation ullamcorper suscipit lobortis nisl ut aliquip ex ea commodo consequat. Duis dolore te feugait nulla facilisi. Nam liber tempor cum soluta nobis eleifend option congue nihil imperdiet doming id quod mazim placerat facer possim assum. Lorem ipsum dolor sit amet, consectetuer adipiscing elit, sed diam nonummy nibh euismod tincidunt ut laoreet dolore magna aliquam erat volutpat. Ut wisi enim ad minim veniam, quis nostrud exerci tation ullamcorper suscipit lobortis nisl ut aliquip ex ea commodo consequat.</p>
        <p>Consectetuer adipiscing elit, sed diam nonummy nibh euismod tincidunt ut laoreet dolore magna aliquam erat volutpat. Ut wisi enim ad minim veniam, quis nostrud exerci tation ullamcorper suscipit lobortis nisl ut aliquip ex ea commodo consequat. Consectetuer adipiscing elit, sed diam nonummy nibh euismod tincidunt ut laoreet dolore magna aliquam erat volutpat. Ut wisi enim ad minim veniam, quis nostrud exerci tation ullamcorper suscipit lobortis nisl ut aliquip ex ea commodo consequat.</p>
        <p>Consectetuer adipiscing elit, sed diam nonummy nibh euismod tincidunt ut laoreet dolore magna aliquam erat volutpat. Ut wisi enim ad minim veniam, quis nostrud exerci tation ullamcorper suscipit lobortis nisl ut aliquip ex ea commodo consequat. Consectetuer adipiscing elit, sed diam nonummy nibh euismod tincidunt ut laoreet dolore magna aliquam erat volutpat. Ut wisi enim ad minim veniam, quis nostrud exerci tation ullamcorper suscipit lobortis nisl ut aliquip ex ea commodo consequat.</p>
      </div>
      <p class="closing">Sincerely Yours</p>
      <span class="signature" role="img" aria-label="Handwritten signature of Walter Pendleton"></span>
    </section>

    <footer>
      <div class="contact-row">
        <div class="attorney">
          <div class="attorney-name">Anselmo R Quintara III</div>
          <div>Attorney at Law</div>
        </div>
        <span class="divider"></span>
        <ul class="contact-list">
          <li><svg viewBox="0 0 10 10"><path d="M2 0h2l1 3-1.5 1a6 6 0 0 0 2.5 2.5L7 5l3 1v2a2 2 0 0 1-2 2A8 8 0 0 1 0 2a2 2 0 0 1 2-2z"/></svg>877-482-6017</li>
          <li><svg viewBox="0 0 10 10"><rect x="2" y="0" width="6" height="3"/><rect x="0" y="3" width="10" height="5" rx="1"/><rect x="2" y="7" width="6" height="3"/></svg>469-738-1452</li>
        </ul>
        <span class="divider"></span>
        <ul class="contact-list">
          <li><svg viewBox="0 0 10 10"><path d="M0 2h10v6H0z"/></svg>bry@bry7legal.example</li>
          <li><svg viewBox="0 0 10 10"><circle cx="5" cy="5" r="5"/></svg>www.bry7legal.example</li>
        </ul>
      </div>
      <span class="footer-mark"></span>
      <span class="footer-block"></span>
      <div class="footer-band">2847 Larkspur Blvd, Ste 300, Dallas, TX 75204</div>
    </footer>
  </main>
</body>
</html>
```